(2) Graphics for Online Store. Creative Minds Welcome+

Need (2) Different Graphics for an Online Store selling digital goods.

The digital goods are 'Leads' for Business Loan Brokers. The graphic should resemble 'Money' in some creative way.

#1 Aged Business Funding Leads
# 2 'Business Funding Real Time Calls

Preferred Colors: White/Black/Aqua

Examples of each included below. Not looking for replicas. The attached are examples of similar products only. No Clipart Please! Needs to be a Professional Clean Look! Do not replicate or emulate the attached. This is just an example.

```html
<!DOCTYPE html>
<html lang="en">
<head>
<meta charset="UTF-8">
<title>Aged Business Loan Leads Banner</title>
<link rel="stylesheet" href="https://fonts.googleapis.com/css2?family=Bebas+Neue&family=Michroma&family=Orbitron:wght@900&display=swap">
<style>
  :root {
    --page: #ffffff;
    --navy-deep: #060e22;
    --navy: #0c1f3d;
    --teal-dark: #0f5a66;
    --aqua: #19c2dc;
    --aqua-light: #8fe6f5;
    --aqua-ribbon: #2fb3dd;
    --white: #ffffff;
    --gold: #e0a92a;
    --gold-light: #f7d56a;
    --drone-grey: #8a8f99;
  }
  html, body {
    margin: 0;
    padding: 0;
    width: 1200px;
    height: 1200px;
    overflow: hidden;
    background: var(--page);
  }
  .banner {
    position: absolute;
    left: 136px;
    top: 342px;
    width: 928px;
    height: 516px;
    display: block;
    box-shadow: 0 2px 8px rgba(0,0,0,0.35);
  }
  .headline-top, .headline-bottom {
    font-family: "Michroma", sans-serif;
    fill: var(--white);
  }
  .headline-main {
    font-family: "Bebas Neue", sans-serif;
    fill: var(--aqua);
  }
  .ribbon-text, .badge-label {
    font-family: "Bebas Neue", sans-serif;
    fill: var(--white);
  }
  .badge-number {
    font-family: "Orbitron", sans-serif;
    font-weight: 900;
    fill: var(--white);
  }
  .dollar-mark {
    font-family: "Bebas Neue", sans-serif;
    fill: url(#goldGrad);
  }
  .ring { fill: none; stroke: var(--white); stroke-width: 1.6; opacity: 0.85; }
</style>
</head>
<body>
<svg class="banner" viewBox="0 0 990 550" xmlns="http://www.w3.org/2000/svg">
  <defs>
    <linearGradient id="bgGrad" x1="0" y1="0" x2="1" y2="1">
      <stop offset="0" stop-color="var(--navy-deep)"/>
      <stop offset="0.55" stop-color="var(--navy)"/>
      <stop offset="1" stop-color="#12304f"/>
    </linearGradient>
    <linearGradient id="badgeGrad" x1="0" y1="0" x2="0" y2="1">
      <stop offset="0" stop-color="var(--aqua-light)"/>
      <stop offset="0.5" stop-color="#3fcde6"/>
      <stop offset="1" stop-color="#17a9cf"/>
    </linearGradient>
    <linearGradient id="ribbonGrad" x1="0" y1="0" x2="0" y2="1">
      <stop offset="0" stop-color="#4cc6ec"/>
      <stop offset="1" stop-color="#1e93c6"/>
    </linearGradient>
    <linearGradient id="goldGrad" x1="0" y1="0" x2="0" y2="1">
      <stop offset="0" stop-color="var(--gold-light)"/>
      <stop offset="1" stop-color="var(--gold)"/>
    </linearGradient>
  </defs>

  <!-- background -->
  <rect class="backdrop" width="990" height="550" fill="url(#bgGrad)" role="img" aria-label="Dark blue backdrop of banknotes and trading charts"/>
  <path class="corner-wave-top" d="M0 0 H190 C120 20 60 70 40 140 C30 180 12 200 0 205 Z" fill="var(--teal-dark)" opacity="0.75"/>
  <path class="corner-wave-bottom" d="M640 550 C700 520 800 500 880 505 C930 508 965 500 990 490 V550 Z" fill="var(--teal-dark)" opacity="0.85"/>
  <path class="corner-arc" d="M0 50 C40 40 75 20 95 0" fill="none" stroke="var(--white)" stroke-width="1.5" opacity="0.8"/>
  <path class="corner-arc" d="M0 75 C55 60 100 30 118 0" fill="none" stroke="var(--white)" stroke-width="1.5" opacity="0.6"/>

  <!-- target rings -->
  <circle class="ring" cx="790" cy="405" r="62"/>
  <circle class="ring" cx="790" cy="405" r="135"/>
  <circle class="ring" cx="790" cy="405" r="205"/>

  <!-- floor bar -->
  <rect class="floor-bar" x="0" y="462" width="990" height="40" fill="#1c3b63" opacity="0.5"/>

  <!-- drone -->
  <rect class="drone" x="415" y="20" width="145" height="35" rx="8" fill="var(--drone-grey)" role="img" aria-label="Small drone illustration"/>

  <!-- headline -->
  <text class="headline-top" x="62" y="125" font-size="58" textLength="511" lengthAdjust="spacingAndGlyphs">COMMISSON</text>
  <text class="headline-main" x="60" y="290" font-size="226" textLength="515" lengthAdjust="spacingAndGlyphs">MONEY</text>
  <text class="headline-bottom" x="62" y="338" font-size="58" textLength="511" lengthAdjust="spacingAndGlyphs">JUST WAITING</text>

  <!-- ribbon -->
  <path class="ribbon" d="M35 360 H688 L713 393 L688 427 H35 L58 393 Z" fill="url(#ribbonGrad)"/>
  <text class="ribbon-text" x="73" y="412" font-size="46" textLength="597" lengthAdjust="spacingAndGlyphs">AGED BUSINESS LOAN LEADS 100 LEADS</text>

  <!-- coins -->
  <rect class="coin-stack" x="30" y="445" width="170" height="95" rx="6" fill="var(--gold)" role="img" aria-label="Stacks of gold coins"/>
  <rect class="coin-stack" x="495" y="435" width="140" height="90" rx="6" fill="var(--gold)" role="img" aria-label="Stacks of gold coins"/>
  <text class="dollar-mark" x="335" y="522" font-size="100">$</text>

  <!-- aged badge -->
  <path class="badge-arrow" d="M770 72 C700 55 640 90 625 150 L608 146 L628 192 L660 158 L643 155 C655 110 700 90 760 98 Z" fill="#2a9fd8"/>
  <rect class="badge" x="665" y="70" width="278" height="277" rx="30" fill="url(#badgeGrad)"/>
  <text class="badge-number" x="688" y="230" font-size="132" textLength="162" lengthAdjust="spacingAndGlyphs">10</text>
  <text class="badge-number" x="862" y="160" font-size="72">+</text>
  <line x1="688" y1="255" x2="917" y2="255" stroke="var(--white)" stroke-width="2"/>
  <text class="badge-label" x="688" y="304" font-size="64" textLength="229" lengthAdjust="spacingAndGlyphs">DAYS AGED</text>
  <line x1="688" y1="311" x2="917" y2="311" stroke="var(--white)" stroke-width="2"/>

  <text class="dollar-mark" x="765" y="448" font-size="108">$</text>
</svg>
</body>
</html>
```